My project benefits Military, First Responders, Police, Fire, and Educators.

Contact Information for Business Card

2 Sided appointment card. Visual side will have my head shot with "Brisk Lantern" in a bold graffic/text. I am picturing maybe the headshot applied to a filter that has a matrix effect where the picture is made up of data/numbers flowing vertically through the photo. I am of course open to other concepts as well. Side two will have contact info presented in an attractive visual complimenting the front.

```html
<!DOCTYPE html>
<html lang="en">
<head>
<meta charset="utf-8">
<title>Brisk Lantern – Appointment Card</title>
<link rel="stylesheet" href="https://fonts.googleapis.com/css2?family=Anton&family=Open+Sans:wght@400;600;700&display=swap">
<style>
  :root {
    --page: #ecebe8;
    --card: #ffffff;
    --ink: #262626;
    --ink-soft: #3a3a3a;
    --navy: #0d1222;
    --lavender: #a9abd6;
    --rule: #555555;
    --white: #ffffff;
  }
  * { box-sizing: border-box; margin: 0; padding: 0; }
  html, body {
    width: 1200px; height: 900px; overflow: hidden;
    background: var(--page);
    font-family: "Open Sans", Arial, sans-serif;
    color: var(--ink);
  }
  .card {
    position: absolute;
    width: 600px; height: 343px;
    background: var(--card);
    overflow: hidden;
    box-shadow: 0 10px 28px rgba(0,0,0,.18);
  }

  /* Back side: appointment */
  .card-back { left: 90px; top: 70px; }
  .card-back .band {
    position: absolute; left: 0; right: 0; top: 52px; height: 58px;
    background: var(--ink);
  }
  .card-back .brand-seal {
    position: absolute; left: 50%; top: 22px; transform: translateX(-50%);
    display: flex; align-items: center; gap: 14px;
    padding: 0 22px; height: 118px;
    background: var(--ink);
    border-radius: 59px;
    box-shadow: 0 0 0 10px var(--card);
  }
  .card-back .brand-seal .dot {
    width: 34px; height: 34px; border-radius: 50%; background: var(--white);
  }
  .card-back .brand-seal .brand-name {
    font-family: "Anton", Impact, sans-serif;
    font-size: 30px; letter-spacing: 1px; color: var(--white);
    text-transform: uppercase;
  }
  .appointment-label { position: absolute; left: 70px; top: 176px; }
  .appointment-label .lead { font-size: 16px; color: var(--ink-soft); line-height: 1.3; }
  .appointment-label .title { font-size: 30px; color: var(--ink); line-height: 1.1; }
  .write-line { position: absolute; height: 1px; background: var(--rule); }
  .write-line.l1 { left: 250px; right: 40px; top: 168px; }
  .write-line.l2 { left: 70px; right: 40px; top: 244px; }
  .write-line.l3 { left: 70px; right: 40px; top: 292px; }
  .notice {
    position: absolute; left: 0; right: 0; top: 303px;
    text-align: center; font-size: 13px; color: var(--ink-soft);
  }

  /* Front side: contact */
  .card-front { left: 510px; top: 480px; }
  .card-front .waves { position: absolute; inset: 0; }
  .card-front .headshot {
    position: absolute; left: 398px; top: 18px; width: 180px; height: 176px;
    border-radius: 90px 90px 0 0;
    background: linear-gradient(180deg, #b98f74 0%, #c99a80 42%, #28324f 70%, #0d1222 100%);
  }
  .brand-block { position: absolute; left: 44px; top: 28px; }
  .brand-block .dot {
    width: 62px; height: 62px; border-radius: 50%; background: var(--ink);
    margin-left: 48px;
  }
  .brand-block .brand-name {
    font-family: "Anton", Impact, sans-serif;
    font-size: 40px; line-height: 1; color: var(--ink);
    text-transform: uppercase; margin-top: 8px; letter-spacing: .5px;
  }
  .person { position: absolute; left: 48px; top: 146px; }
  .person .name { font-weight: 700; font-size: 20px; color: var(--ink); line-height: 1.35; }
  .person .role { font-size: 15px; color: var(--ink-soft); line-height: 1.35; }
  .contact-list { list-style: none; margin-top: 8px; }
  .contact-list li {
    display: flex; align-items: center; gap: 8px;
    font-size: 16px; color: var(--ink); line-height: 1.4;
  }
  .contact-list svg { width: 14px; height: 14px; fill: var(--ink); }
  .website {
    position: absolute; right: 26px; top: 246px;
    font-size: 14px; color: var(--white);
  }
</style>
</head>
<body>

<section class="card card-back" aria-label="Appointment side">
  <div class="band"></div>
  <div class="brand-seal">
    <span class="dot"></span>
    <span class="brand-name">Brisk Lantern</span>
  </div>
  <div class="write-line l1"></div>
  <div class="appointment-label">
    <div class="lead">Your Next</div>
    <div class="title">Appointment :</div>
  </div>
  <div class="write-line l2"></div>
  <div class="write-line l3"></div>
  <p class="notice">Please give 24 hours notice if you need to reschedule your appointment</p>
</section>

<section class="card card-front" aria-label="Contact side">
  <svg class="waves" viewBox="0 0 600 343" preserveAspectRatio="none" aria-hidden="true">
    <path d="M0,298 C260,298 400,262 470,176 L600,176 L600,343 L0,343 Z" fill="var(--lavender)"/>
    <path d="M0,312 C270,312 410,276 482,190 L600,190 L600,343 L0,343 Z" fill="var(--navy)"/>
  </svg>
  <div class="headshot" role="img" aria-label="Headshot of Marcus Hale in a dark suit and tie"></div>
  <div class="brand-block">
    <div class="dot"></div>
    <div class="brand-name">Brisk Lantern</div>
  </div>
  <div class="person">
    <div class="name">Marcus Hale</div>
    <div class="role">Managing Director</div>
    <ul class="contact-list">
      <li>
        <svg viewBox="0 0 16 16" aria-hidden="true"><path d="M3 2h3l1.5 3.5-2 1.2a8 8 0 0 0 3.8 3.8l1.2-2L14 10v3a1 1 0 0 1-1 1A11 11 0 0 1 2 3a1 1 0 0 1 1-1z"/></svg>
        (044)555018274
      </li>
      <li>
        <svg viewBox="0 0 16 16" aria-hidden="true"><path d="M1 3h14v10H1z M2 4l6 5 6-5" fill="none" stroke="var(--ink)" stroke-width="1.6"/></svg>
        hello@brisklantern.com
      </li>
    </ul>
  </div>
  <div class="website">www.brisklantern.com</div>
</section>

</body>
</html>
```